Modern Medical Optometry Website

We need mordern, Patient friendly website. Easy to navigate and enhance our advance medical technology and excellent patient care.
1. HOME PAGE
2. OUR TEAM PAGE
3. EYECARE PAGE - VISION SERVICES, EYE EXAMS, KERATOCONUS CENTER, GLAUCOMA , DIABITES, MELORIDEX EXAM, DIGITAL RETINAL, OCT.
4. MYOPIA CONTROL CLINIC
5. DRY EYE CLINIC
6. EYEWEAR
7. PATIENT CENTER - BLOG
7. CONTACT US
This is our current website www.brivaloka.com
and We want to add more content and a cleaner design like these website
http://tarnwickfolvendale.com/
https://www.qmvorlu.com/

```html
<!DOCTYPE html>
<html lang="en">
<head>
<meta charset="utf-8">
<title>Brivaloka Optometry</title>
<link href="https://fonts.googleapis.com/css2?family=Montserrat:wght@400;500;600;700&display=swap" rel="stylesheet">
<style>
:root{
  --yellow:#f5c400;
  --black:#111111;
  --ink:#222222;
  --muted:#555555;
  --gray:#ebebeb;
  --nav:#e4e4e4;
  --white:#ffffff;
  --footer-muted:#bbbbbb;
}
*{box-sizing:border-box;margin:0;padding:0}
html,body{width:1200px;height:3719px;overflow:hidden}
body{position:relative;font-family:"Montserrat",Arial,sans-serif;color:var(--ink);background:var(--white)}
.abs{position:absolute}
.yellow{color:var(--yellow)}
.btn{position:absolute;display:flex;align-items:center;justify-content:center;font-weight:600;font-size:15px}
.btn-yellow{background:var(--yellow);color:var(--black)}
.btn-black{background:var(--black);color:var(--white)}
.btn-outline{background:var(--white);border:3px solid var(--yellow);color:var(--black)}
.photo{position:absolute}

/* top bar */
.topbar{left:0;top:0;width:1200px;height:37px;background:var(--yellow)}
.topbar .dots{left:112px;top:11px;display:flex;gap:12px}
.topbar .dots span{width:14px;height:14px;border-radius:50%;background:var(--black)}
.topbar .mail{right:110px;top:0;height:37px;padding:0 22px;display:flex;align-items:center;gap:8px;font-size:15px;border-left:1px solid rgba(0,0,0,.2)}

/* header */
.header{left:0;top:37px;width:1200px;height:119px;background:var(--white)}
.call{left:140px;top:62px;display:flex;align-items:center;gap:20px}
.call .circle{width:56px;height:56px;border-radius:50%;background:var(--yellow);display:flex;align-items:center;justify-content:center}
.call b{display:block;font-size:16px;font-weight:600}
.call span{font-size:15px}
.brand{left:538px;top:42px;width:126px;height:174px;background:var(--white);z-index:3;display:flex;flex-direction:column;align-items:center;justify-content:center;gap:14px;box-shadow:0 2px 6px rgba(0,0,0,.1)}
.brand .mark{width:46px;height:46px;background:var(--yellow)}
.brand .name{font-size:14px;font-weight:600;text-align:center;line-height:1.3;color:var(--ink)}
.appt{left:783px;top:74px;width:209px;height:50px;font-size:14px}

/* nav */
.nav{left:0;top:156px;width:1200px;height:60px;background:var(--nav);font-size:15px}
.nav a{position:absolute;top:20px;color:var(--ink);text-decoration:none}

/* hero */
.hero-bg{left:0;top:216px;width:1200px;height:535px;background:linear-gradient(100deg,#f4f4f4 0%,#e9e9ea 40%,#c9ccd0 70%,#6d7a88 100%)}
.hero-title{left:94px;top:342px;font-size:40px;font-weight:700;letter-spacing:.5px;white-space:nowrap}
.hero-text{left:94px;top:405px;width:480px;font-size:20px;line-height:38px}
.hero-b1{left:94px;top:498px;width:184px;height:50px;font-size:14px}
.hero-b2{left:297px;top:498px;width:181px;height:50px;font-size:14px}

/* service cards */
.card{background:var(--white);box-shadow:0 2px 12px rgba(0,0,0,.18);text-align:center}
.card .img{position:absolute;left:22px;top:22px;width:calc(100% - 44px);height:181px}
.card h3{position:absolute;left:0;width:100%;top:226px;font-size:19px;font-weight:700}
.card p{position:absolute;left:22px;right:22px;top:260px;font-size:11.5px;line-height:21px;color:var(--muted)}
.card .more{position:absolute;left:0;width:100%;top:382px;font-size:14px;font-weight:700}

/* about */
.about-title{left:102px;top:1172px;font-size:26px;font-weight:700;white-space:nowrap}
.about-text{left:102px;top:1218px;width:495px;font-size:14.5px;line-height:31px;text-align:justify}
.about-b1{left:102px;top:1391px;width:181px;height:47px}
.about-b2{left:300px;top:1391px;width:178px;height:47px}

/* doctors */
.doctors{left:0;top:1522px;width:1200px;height:536px;background:var(--gray)}
.sec-title{width:1200px;left:0;text-align:center;font-weight:700;font-size:34px}
.doc .accent-top{position:absolute;left:50%;transform:translateX(-50%);top:-12px;width:90px;height:12px;background:var(--yellow)}
.doc .accent-side{position:absolute;top:130px;height:90px;width:12px;background:var(--yellow)}
.doc .name{position:absolute;left:0;bottom:0;width:100%;height:57px;background:var(--yellow);display:flex;align-items:center;justify-content:center;font-weight:700;font-size:19px}
.arrow{position:absolute}

/* eyewear */
.eyewear-title{left:607px;top:2130px;font-size:34px;font-weight:700}
.eyewear-text{left:607px;top:2185px;width:500px;font-size:15px;line-height:32px;text-align:justify}
.eyewear-b1{left:607px;top:2385px;width:181px;height:49px}

/* advantages */
.advantages{left:0;top:2516px;width:1200px;height:434px;background:var(--gray)}
.adv-item{position:absolute;width:320px;text-align:center}
.adv-item h4{font-size:16px;font-weight:700;margin-top:18px}
.adv-item p{font-size:12px;line-height:24px;margin-top:8px;font-weight:500}

/* testimonials */
.testi-text{left:160px;top:3125px;width:880px;text-align:center;font-size:19px;line-height:36px;color:var(--muted)}

/* footer */
.footer{left:0;top:3334px;width:1200px;height:385px;background:#000}
.finfo{position:absolute;width:280px;text-align:center;font-size:16px;line-height:30px;color:var(--white)}
.finfo .circ{width:89px;height:89px;border-radius:50%;background:var(--yellow);margin:0 auto 20px;display:flex;align-items:center;justify-content:center}
.flinks{left:0;top:3590px;width:1200px;text-align:center;font-size:15px;color:var(--white)}
.flinks span{margin:0 8px}
.copy{left:0;top:3630px;width:1200px;text-align:center;font-size:14px;color:var(--footer-muted)}
.fsocial{left:0;top:3672px;width:1200px;display:flex;justify-content:center;gap:10px}
.fsocial span{width:32px;height:32px;border-radius:50%;border:2px solid var(--white)}
</style>
</head>
<body>

<!-- top bar -->
<div class="abs topbar">
  <div class="abs dots"><span></span><span></span><span></span><span></span><span></span><span></span><span></span></div>
  <div class="abs mail">
    <svg width="16" height="12" viewBox="0 0 16 12"><rect width="16" height="12" fill="#111"/><path d="M0 0 L8 7 L16 0" stroke="#f5c400" stroke-width="1.5" fill="none"/></svg>
    info@brivaloka.com
  </div>
</div>

<!-- header -->
<div class="abs header"></div>
<div class="abs call">
  <div class="circle">
    <svg width="28" height="28" viewBox="0 0 24 24"><path fill="#fff" d="M6.6 10.8a15.1 15.1 0 0 0 6.6 6.6l2.2-2.2c.3-.3.7-.4 1-.2 1.1.4 2.3.6 3.6.6.6 0 1 .4 1 1V20c0 .6-.4 1-1 1A17 17 0 0 1 3 4c0-.6.4-1 1-1h3.5c.6 0 1 .4 1 1 0 1.3.2 2.5.6 3.6.1.3 0 .7-.2 1z"/></svg>
  </div>
  <div><b>CALL OR TEXT US</b><span>818-555-0142</span></div>
</div>
<div class="abs brand"><div class="mark"></div><div class="name">BRIVALOKA<br>OPTOMETRY</div></div>
<div class="btn btn-yellow appt">MAKE AN APPOINTMENT</div>

<!-- nav -->
<nav class="abs nav">
  <a style="left:100px">Home</a>
  <a style="left:172px">Our Team</a>
  <a style="left:268px">Eyecare</a>
  <a style="left:355px">Myopia Control Clinic</a>
  <a style="left:686px">Dry Eye Clinic</a>
  <a style="left:812px">Eyewear</a>
  <a style="left:903px">Patient Center</a>
  <a style="left:1033px">Contact</a>
</nav>

<!-- hero -->
<div class="abs hero-bg" role="img" aria-label="Optometrist pointing at an eye chart while a patient watches"></div>
<h1 class="abs hero-title"><span class="yellow">BRIVALOKA</span> OPTOMETRY</h1>
<p class="abs hero-text">Sed ut perspiciatis unde omnis iste natus error sit voluptatem accusantium</p>
<div class="btn btn-yellow hero-b1">FREE CONSULTATION</div>
<div class="btn btn-black hero-b2">READ MORE</div>

<!-- service cards -->
<div class="abs card" style="left:99px;top:669px;width:317px;height:422px">
  <div class="img" role="img" aria-label="Smiling woman in glasses in front of an eye chart" style="background:linear-gradient(135deg,#e8e2d6,#b89a78)"></div>
  <h3 class="yellow">VISION SERVICES</h3>
  <p>Sed ut perspiciatis unde omnis iste natus error sit voluptatem accusantium doloremque laudant, totam rem aperiam, eaque ipsa quae ab illo inventore veritatis et quasi architecto beatae vitae dicta sunt explicabo.</p>
  <div class="more">Read More</div>
</div>
<div class="abs card" style="left:444px;top:627px;width:315px;height:424px">
  <div class="img" role="img" aria-label="Patient at a slit lamp during an eye exam" style="background:linear-gradient(135deg,#c7ccd2,#6e7780)"></div>
  <h3>EYE EXAMS</h3>
  <p>Sed ut perspiciatis unde omnis iste natus error sit voluptatem accusantium doloremque laudant, totam rem aperiam, eaque ipsa quae ab illo inventore veritatis et quasi architecto beatae vitae dicta sunt explicabo.</p>
  <div class="more">Read More</div>
</div>
<div class="abs card" style="left:783px;top:669px;width:318px;height:422px">
  <div class="img" role="img" aria-label="Close-up of an eye lit in purple light" style="background:linear-gradient(135deg,#3a2a6a,#b06ad8)"></div>
  <h3 class="yellow">DRY EYE CLINIC</h3>
  <p>Sed ut perspiciatis unde omnis iste natus error sit voluptatem accusantium doloremque laudant, totam rem aperiam, eaque ipsa quae ab illo inventore veritatis et quasi architecto beatae vitae dicta sunt explicabo.</p>
  <div class="more">Read More</div>
</div>

<!-- about -->
<h2 class="abs about-title">ABOUT <span class="yellow">THE BRIVALOKA PROMISE</span></h2>
<p class="abs about-text">Welcome to Brivaloka Optometry, where your vision and eye health are our sole priority. We take great pride in providing you with state-of-the-art eyecare matched with personal attention from our staff and doctors. Your quality of life is our goal and we believe that healthy eyesight is vital to achieving it.</p>
<div class="btn btn-yellow about-b1">Read More</div>
<div class="btn btn-outline about-b2">Our Services</div>
<div class="photo" role="img" aria-label="Woman putting in a contact lens" style="left:617px;top:1163px;width:243px;height:142px;background:linear-gradient(135deg,#d9d4cf,#8b7a6e)"></div>
<div class="photo" role="img" aria-label="Close-up of a contact lens on a fingertip" style="left:866px;top:1163px;width:243px;height:142px;background:linear-gradient(135deg,#b9c9d0,#6d8690)"></div>
<div class="photo" role="img" aria-label="Close-up of a pair of eyes" style="left:617px;top:1311px;width:243px;height:144px;background:linear-gradient(135deg,#c6a58e,#7d5b48)"></div>
<div class="photo" role="img" aria-label="Two friends trying on eyewear" style="left:866px;top:1311px;width:243px;height:144px;background:linear-gradient(135deg,#e4dcd5,#a08d84)"></div>

<!-- doctors -->
<div class="abs doctors"></div>
<div class="abs sec-title" style="top:1570px">MEET <span class="yellow">OUR DOCTORS</span></div>
<svg class="arrow" style="left:40px;top:1802px" width="36" height="30" viewBox="0 0 36 30"><path d="M34 15H4M14 4L3 15l11 11" stroke="#333" stroke-width="3" fill="none"/></svg>
<svg class="arrow" style="left:1124px;top:1802px" width="36" height="30" viewBox="0 0 36 30"><path d="M2 15h30M22 4l11 11-11 11" stroke="#333" stroke-width="3" fill="none"/></svg>

<div class="abs doc" style="left:99px;top:1641px;width:303px;height:352px">
  <div class="accent-top"></div><div class="accent-side" style="left:-12px"></div><div class="accent-side" style="right:-12px"></div>
  <div class="photo" role="img" aria-label="Portrait of the first optometrist" style="left:0;top:0;width:303px;height:295px;background:linear-gradient(180deg,#f3efe9,#c9b6a4)"></div>
  <div class="name">DR. MINA SOLVAY, O.D.</div>
</div>
<div class="abs doc" style="left:449px;top:1641px;width:305px;height:352px">
  <div class="accent-top"></div><div class="accent-side" style="left:-12px"></div><div class="accent-side" style="right:-12px"></div>
  <div class="photo" role="img" aria-label="Portrait of the second optometrist" style="left:0;top:0;width:305px;height:295px;background:linear-gradient(180deg,#9bb36a,#c3b39c)"></div>
  <div class="name">DR. RENA OKALUMA</div>
</div>
<div class="abs doc" style="left:798px;top:1641px;width:303px;height:352px">
  <div class="accent-top"></div><div class="accent-side" style="left:-12px"></div><div class="accent-side" style="right:-12px"></div>
  <div class="photo" role="img" aria-label="Portrait of the third team member" style="left:0;top:0;width:303px;height:295px;background:linear-gradient(180deg,#a9bb78,#cbb9a4)"></div>
  <div class="name" style="font-size:18px">TESSA LINWOLD</div>
</div>

<!-- eyewear -->
<div class="abs" style="left:107px;top:2132px;width:463px;height:297px;background:var(--yellow)"></div>
<div class="photo" role="img" aria-label="Child wearing a trial frame at the optical bench" style="left:126px;top:2152px;width:454px;height:292px;background:linear-gradient(135deg,#e6e4e1,#9ea4aa)"></div>
<h2 class="abs eyewear-title">EYE WEAR</h2>
<p class="abs eyewear-text">Sed ut perspiciatis unde omnis iste natus error sit voluptatem accusantium doloremque laudantium, totam rem aperiam, eaque ipsa quae ab illo inventore veritatis et quasi architecto beatae vitae dicta sunt explicabo. Nemo enim ipsam voluptatem quia voluptas sit aspernatur aut odit aut fugit, sed quia consequuntur magni dolores eos qui ratione voluptatem sequi nesciunt.</p>
<div class="btn btn-yellow eyewear-b1">Read More</div>

<!-- advantages -->
<div class="abs advantages"></div>
<div class="abs sec-title" style="top:2580px;font-size:17px;font-weight:600">Our Advantages</div>
<div class="abs sec-title" style="top:2608px">WHY CUSTOMERS <span class="yellow">CHOOSE US</span></div>
<div class="abs" style="left:190px;top:2668px;width:820px;text-align:center;font-size:15px;line-height:32px;font-weight:500">At vero eos et accusamus et iusto odio dignissimos ducimus qui blanditiis praesentium voluptatum deleniti atque corrupti quos dolores</div>

<div class="adv-item" style="left:91px;top:2752px">
  <svg width="34" height="34" viewBox="0 0 24 24"><path fill="#f5c400" d="M6 2h12v3h4v3a5 5 0 0 1-5 5 6 6 0 0 1-4 3v3h4v3H7v-3h4v-3a6 6 0 0 1-4-3 5 5 0 0 1-5-5V5h4zM4 7v1a3 3 0 0 0 2.3 2.9A7 7 0 0 1 6 9V7zm16 0h-2v2a7 7 0 0 1-.3 1.9A3 3 0 0 0 20 8z"/></svg>
  <h4>CERTIFIED SPECIALISTS</h4>
  <p>At vero eos et accusamus et iusto odio dignis ducimus qui blanditiis praesentium</p>
</div>
<div class="adv-item" style="left:440px;top:2752px">
  <svg width="36" height="34" viewBox="0 0 26 24"><path fill="#f5c400" d="M3 2h14a2 2 0 0 1 2 2v8a2 2 0 0 1-2 2H9l-4 4v-4H3a2 2 0 0 1-2-2V4a2 2 0 0 1 2-2zm18 6h2a2 2 0 0 1 2 2v7a2 2 0 0 1-2 2h-1v3l-3-3h-7a2 2 0 0 1-2-2v-1h7a4 4 0 0 0 4-4z"/></svg>
  <h4>100% POSITIVE FEEDBACK</h4>
  <p>At vero eos et accusamus et iusto odio dignis ducimus qui blanditiis praesentium</p>
</div>
<div class="adv-item" style="left:788px;top:2752px">
  <svg width="48" height="34" viewBox="0 0 48 34"><rect x="2" y="2" width="44" height="30" fill="#f5c400"/></svg>
  <h4>MAKE A PAYMENT ONLINE</h4>
  <p>At vero eos et accusamus et iusto odio dignis ducimus qui blanditiis praesentium</p>
</div>

<!-- testimonials -->
<div class="abs sec-title yellow" style="top:3010px">TESTIMONIALS</div>
<svg class="abs" style="left:573px;top:3068px" width="54" height="40" viewBox="0 0 54 40"><path fill="#444" d="M2 40V22C2 10 8 3 20 0l2 5c-6 2-9 6-9 12h9v23zm30 0V22C32 10 38 3 50 0l2 5c-6 2-9 6-9 12h9v23z"/></svg>
<p class="abs testi-text">Sed ut perspiciatis unde omnis iste natus error sit voluptatem accusantium doloremque laudantium, totam rem aperiam, eaque ipsa quae ab illo inventore veritatis et quasi architecto beatae vitae dicta sunt explicabo.</p>
<div class="abs sec-title" style="top:3248px;font-size:18px;font-weight:600">Ellis Varden</div>
<svg class="arrow" style="left:66px;top:3124px" width="66" height="44" viewBox="0 0 66 44"><path d="M64 22H6M24 4L5 22l19 18" stroke="#333" stroke-width="4" fill="none"/></svg>
<svg class="arrow" style="left:1068px;top:3124px" width="66" height="44" viewBox="0 0 66 44"><path d="M2 22h58M42 4l19 18-19 18" stroke="#333" stroke-width="4" fill="none"/></svg>

<!-- footer -->
<footer class="abs footer"></footer>
<div class="finfo" style="left:182px;top:3402px">
  <div class="circ"><svg width="40" height="44" viewBox="0 0 24 26"><path d="M12 1a8 8 0 0 0-8 8c0 6 8 14 8 14s8-8 8-14a8 8 0 0 0-8-8z" fill="none" stroke="#111" stroke-width="1.8"/><circle cx="12" cy="9" r="3" fill="none" stroke="#111" stroke-width="1.8"/><ellipse cx="12" cy="24" rx="7" ry="1.5" fill="none" stroke="#111" stroke-width="1.2"/></svg></div>
  4820 Marrow Lane,<br>Feldbrook, CA 90000
</div>
<div class="finfo" style="left:485px;top:3402px">
  <div class="circ"><svg width="40" height="40" viewBox="0 0 24 24"><path fill="none" stroke="#111" stroke-width="1.8" d="M6.6 10.8a15.1 15.1 0 0 0 6.6 6.6l2.2-2.2c.3-.3.7-.4 1-.2 1.1.4 2.3.6 3.6.6.6 0 1 .4 1 1V20c0 .6-.4 1-1 1A17 17 0 0 1 3 4c0-.6.4-1 1-1h3.5c.6 0 1 .4 1 1 0 1.3.2 2.5.6 3.6.1.3 0 .7-.2 1z"/></svg></div>
  Phone:<br>818-555-0142
</div>
<div class="finfo" style="left:790px;top:3402px">
  <div class="circ"><svg width="44" height="32" viewBox="0 0 44 32"><rect x="2" y="2" width="40" height="28" fill="none" stroke="#111" stroke-width="2.5"/><path d="M2 2l20 16L42 2M2 30l15-14M42 30L27 16" fill="none" stroke="#111" stroke-width="2.5"/></svg></div>
  Email:<br>info@brivaloka.com
</div>
<div class="abs flinks">Home<span>|</span>Our Team<span>|</span>Eyecare<span>|</span>Myopia Control Clinic<span>|</span>Dry Eye Clinic<span>|</span>Eyewear<span>|</span>Patient Center<span>|</span>Contact Us</div>
<div class="abs copy">© 2019 Company Name &nbsp;All right reserved</div>
<div class="abs fsocial"><span></span><span></span><span></span><span></span></div>

</body>
</html>
```